Business card for Luxury Portable Restroom Trailer company

We are a Luxury Portable Restroom Trailer Company Called FALCRIDGE HIRES. Based in Orange County California. We provide portable restroom trailers for events, such as, Weddings, Concerts, Charity events, Sporting events, Tournaments, Corporate events, ect. We rent and Sell the Luxury restrooms. Our colors are white, grey, and Orange. As you will see in the logo we uploaded.
There are 2 people in the company so the names and titles will change for the 3 people but card will remain the same. Here is the information for each Person: Dwight Penner CFO 555 318-0476
next Person: Leon Marchetti VP 555 318-0476
Next Person: Owen Marchetti CEO 555 318-0476
Information to include on the card: Luxury Restroom Trailers Rental and Sales. Weddings, Concerts, Charity, Sporting and Corp. Events.

```html
<!DOCTYPE html>
<html lang="en">
<head>
<meta charset="utf-8">
<title>FALCRIDGE HIRES – Business Card</title>
<link href="https://fonts.googleapis.com/css2?family=Nunito+Sans:wght@400;600;800&display=swap" rel="stylesheet">
<style>
  :root {
    --backdrop: #3a3a3a;
    --card-dark: #262626;
    --card-light: #ffffff;
    --orange: #f26522;
    --grey-text: #5a5a5a;
    --grey-mark: #6b6b6b;
    --light-text: #f2f2f2;
    --divider: #cfcfcf;
  }
  * { box-sizing: border-box; margin: 0; padding: 0; }
  html, body { width: 1200px; height: 689px; overflow: hidden; }
  body {
    background: var(--backdrop);
    font-family: "Nunito Sans", Arial, sans-serif;
    position: relative;
  }
  .card {
    position: absolute;
    top: 196px;
    width: 520px;
    height: 297px;
    border-radius: 18px;
    border-bottom: 4px solid var(--orange);
    box-shadow: 0 14px 30px rgba(0,0,0,.35);
    overflow: hidden;
  }
  .card-back { left: 45px; background: var(--card-dark); }
  .card-front { left: 635px; background: var(--card-light); }

  /* back */
  .back-wordmark {
    position: absolute;
    left: 0; right: 0; top: 82px;
    display: flex; align-items: center; justify-content: center; gap: 12px;
  }
  .back-wordmark .mark-square {
    width: 26px; height: 26px; background: var(--grey-mark);
  }
  .back-wordmark .wordmark-text {
    font-weight: 800; font-size: 34px; letter-spacing: 2px; color: var(--grey-mark);
  }
  .back-tagline {
    position: absolute; left: 0; right: 0; top: 190px;
    text-align: center; color: var(--light-text);
    font-size: 15px; line-height: 1.55; font-weight: 400;
  }

  /* front */
  .front-wordmark {
    position: absolute; left: 28px; top: 155px;
    display: flex; align-items: center; gap: 8px;
    white-space: nowrap;
  }
  .front-wordmark .mark-square { width: 18px; height: 18px; background: var(--orange); }
  .front-wordmark .wordmark-text {
    font-weight: 800; font-size: 21px; letter-spacing: .5px; color: var(--orange);
  }
  .front-divider {
    position: absolute; left: 300px; top: 70px; width: 1px; height: 120px;
    background: var(--divider);
  }
  .contact {
    position: absolute; left: 318px; top: 68px;
    white-space: nowrap;
  }
  .contact .person-name {
    color: var(--orange); font-weight: 800; font-size: 19px; letter-spacing: .5px;
  }
  .contact .person-title {
    color: var(--grey-text); font-size: 12px; margin-top: 1px; margin-bottom: 12px;
  }
  .contact-line {
    display: flex; align-items: center; gap: 8px;
    color: var(--grey-text); font-size: 12.5px; line-height: 1.75;
  }
  .contact-line svg { width: 11px; height: 11px; flex: none; }
</style>
</head>
<body>
  <section class="card card-back">
    <div class="back-wordmark">
      <span class="mark-square"></span>
      <span class="wordmark-text">FALCRIDGE HIRES</span>
    </div>
    <p class="back-tagline">
      Luxury Restroom Trailers Rental and Sales.<br>
      Weddings • Concerts • Charity • Sporting and Corp. Events
    </p>
  </section>

  <section class="card card-front">
    <div class="front-wordmark">
      <span class="mark-square"></span>
      <span class="wordmark-text">FALCRIDGE HIRES</span>
    </div>
    <div class="front-divider"></div>
    <div class="contact">
      <h1 class="person-name">DWIGHT PENNER</h1>
      <p class="person-title">CFO</p>
      <p class="contact-line">
        <svg viewBox="0 0 12 12"><path fill="#f26522" d="M2.5 1 4.3 1 5 3.4 3.9 4.3a6.6 6.6 0 0 0 3.8 3.8L8.6 7l2.4.7v1.8c0 .6-.5 1-1 1A9 9 0 0 1 1.5 2c0-.5.4-1 1-1z"/></svg>
        555 318-0476
      </p>
      <p class="contact-line">
        <svg viewBox="0 0 12 12"><rect x="0.5" y="2.5" width="11" height="7.5" fill="#f26522"/><path d="M1 3l5 4 5-4" stroke="#fff" stroke-width="1" fill="none"/></svg>
        info@falcridgehires.com
      </p>
      <p class="contact-line">
        <svg viewBox="0 0 12 12"><circle cx="6" cy="6" r="5.3" fill="#f26522"/><path d="M1 6h10M6 .7c-2 2.8-2 7.8 0 10.6M6 .7c2 2.8 2 7.8 0 10.6" stroke="#fff" stroke-width=".8" fill="none"/></svg>
        www.falcridgehires.com
      </p>
    </div>
  </section>
</body>
</html>
```